ReelBloom business card

We are a performing arts company providing training (to both kids and adults) as well as performers for events. We hope to bring joy and confidence on stage to the people we train, as well as joy to the audience when our artistes perform. Designs should convey the joy, confidence and vibrancy on stage. Design business card using the attached logo. Card to include name, mobile tel, email address, company address, and website. Double sided. To also include the following list of what the company does:
• Training & Enrichment
• Private & Corporate Entertainment
- Music composition & production

Industry/Entity Type

Training

Contact Information for Business Card

Card to include name, mobile tel, email address, company address, and website. Double sided. To also include the following list of what the company does:
• Training & Enrichment

Requirements
Nice to have
• Card need not be the traditional rectangular in shape but not too outrageous.

```html
<!DOCTYPE html>
<html lang="en">
<head>
<meta charset="utf-8">
<title>ReelBloom business card</title>
<link href="https://fonts.googleapis.com/css2?family=Arimo:wght@400;700&family=Tinos:wght@700&display=swap" rel="stylesheet">
<style>
  :root {
    --purple: #6a0a82;
    --purple-text: #7a1e8f;
    --navy: #1f2a5c;
    --white: #ffffff;
    --backdrop: #ece9ee;
    --mark-a: #3c67c9;
    --mark-b: #f2a51d;
    --mark-c: #e23c7a;
  }
  * { box-sizing: border-box; margin: 0; padding: 0; }
  html, body { width: 1200px; height: 848px; overflow: hidden; }
  body {
    background: var(--backdrop);
    font-family: "Arimo", Arial, sans-serif;
    display: flex;
    align-items: center;
    justify-content: center;
    gap: 40px;
  }
  .card {
    width: 540px;
    height: 309px;
    border-radius: 24px;
    background: var(--white);
    overflow: hidden;
    position: relative;
    box-shadow: 0 10px 28px rgba(40, 20, 50, 0.18);
  }

  /* Front */
  .card-front { display: flex; }
  .front-brand {
    width: 41%;
    display: flex;
    flex-direction: column;
    align-items: center;
    justify-content: center;
    gap: 6px;
  }
  .brand-symbol {
    width: 92px;
    height: 92px;
    border-radius: 50%;
    background: radial-gradient(circle at 45% 40%, var(--mark-a), var(--mark-b) 70%, var(--mark-c));
    opacity: 0.85;
  }
  .brand-name {
    font-weight: 700;
    font-size: 38px;
    color: var(--purple);
    letter-spacing: 0.5px;
  }
  .brand-tagline {
    font-size: 15px;
    color: var(--navy);
  }
  .front-contact {
    flex: 1;
    background: var(--purple);
    color: var(--white);
    padding: 34px 26px 0 30px;
  }
  .person-name {
    font-family: "Tinos", "Times New Roman", serif;
    font-weight: 700;
    font-size: 26px;
    line-height: 1;
  }
  .person-title { font-size: 13px; margin-top: 3px; }
  .contact-list { list-style: none; margin-top: 42px; }
  .contact-list li {
    display: flex;
    align-items: flex-start;
    gap: 12px;
    font-size: 13.5px;
    line-height: 1.3;
    margin-bottom: 5px;
  }
  .contact-list svg { width: 14px; height: 14px; flex: none; margin-top: 2px; }

  /* Back */
  .card-back {
    display: flex;
    flex-direction: column;
    align-items: center;
    justify-content: center;
  }
  .back-brand {
    display: flex;
    flex-direction: column;
    align-items: center;
    gap: 4px;
  }
  .back-brand .brand-symbol { width: 70px; height: 70px; }
  .back-brand .brand-name { font-size: 40px; }
  .back-brand .brand-tagline { font-size: 14px; }
  .services {
    list-style: none;
    margin-top: 22px;
    text-align: center;
    color: var(--purple-text);
    font-size: 16px;
    line-height: 1.55;
  }
</style>
</head>
<body>
  <section class="card card-front">
    <div class="front-brand">
      <div class="brand-symbol" role="img" aria-label="Company symbol: colourful dancing performers with music notes"></div>
      <div class="brand-name">ReelBloom</div>
      <div class="brand-tagline">delighting in the arts</div>
    </div>
    <div class="front-contact">
      <div class="person-name">Employee name</div>
      <div class="person-title">Managing Director</div>
      <ul class="contact-list">
        <li>
          <svg viewBox="0 0 16 16" fill="currentColor"><path d="M3.5 1.5l2.5 3-1.5 1.8c.8 1.8 2.3 3.3 4.2 4.2L10.5 9l3 2.5-1.3 2.6c-5.6-.4-10-4.8-10.3-10.4z"/></svg>
          <span>555-0142 7788</span>
        </li>
        <li>
          <svg viewBox="0 0 16 16" fill="none" stroke="currentColor" stroke-width="1.6"><rect x="4" y="1.5" width="8" height="13" rx="1.5"/></svg>
          <span>555-0199 3160</span>
        </li>
        <li>
          <svg viewBox="0 0 16 16" fill="currentColor"><path d="M1 3.5h14v9H1z"/><path d="M1.5 4l6.5 5 6.5-5" fill="none" stroke="#6a0a82" stroke-width="1.2"/></svg>
          <span>hello@reelbloom-arts.com</span>
        </li>
        <li>
          <svg viewBox="0 0 16 16" fill="none" stroke="currentColor" stroke-width="1.5"><circle cx="8" cy="8" r="6.3"/><path d="M1.7 8h12.6M8 1.7c2.2 2.4 2.2 10.2 0 12.6M8 1.7c-2.2 2.4-2.2 10.2 0 12.6"/></svg>
          <span>www.reelbloom-arts.com</span>
        </li>
        <li>
          <svg viewBox="0 0 16 16" fill="currentColor"><path d="M8 1a4.6 4.6 0 0 0-4.6 4.6C3.4 9.4 8 15 8 15s4.6-5.6 4.6-9.4A4.6 4.6 0 0 0 8 1zm0 6.4a1.8 1.8 0 1 1 0-3.6 1.8 1.8 0 0 1 0 3.6z"/></svg>
          <span>Studio 4, 12 Maple Row, Brightvale,<br>NJ 00000</span>
        </li>
      </ul>
    </div>
  </section>

  <section class="card card-back">
    <div class="back-brand">
      <div class="brand-symbol" role="img" aria-label="Company symbol: colourful dancing performers with music notes"></div>
      <div class="brand-name">ReelBloom</div>
      <div class="brand-tagline">delighting in the arts</div>
    </div>
    <ul class="services">
      <li>Training &amp; Enrichment</li>
      <li>Private &amp; Corporate Entertainment</li>
      <li>Music composition &amp; production</li>
    </ul>
  </section>
</body>
</html>
```